New Business card design to reflect rebrand

I would like a business card design with a good base colour for our new logo and also a placeholder for a profile pic of the card holder. the design needs to be editable to the point that we can easily change the picture of the person and use that design for printmerlo etc. we are looking at a metalic finish business card so will need a good base colour to bring out the finish.

Target Market(s)

prospective customers

Industry/Entity Type

Business

Contact Information for Business Card

I would like one editable design that we can change the name of the card holder and profile picture. The design need to be in a format that be send to printmerlo etc.

Our address is Fenwick Lodge, Copse Lane, Ashcombe Vale, GU14 3TP Tel no. 01483 556172

Requirements
Must have
• place holder for a profile pic for the card holder. in AI or preferably PSD format

```html
<!DOCTYPE html>
<html lang="en">
<head>
<meta charset="utf-8">
<title>Norvane Workplace Services – Business Card</title>
<link rel="stylesheet" href="https://fonts.googleapis.com/css2?family=Open+Sans:wght@400;600;700&display=swap">
<style>
  :root {
    --backdrop: #ece9e4;
    --gold-light: #d2b384;
    --gold-mid: #c4a272;
    --gold-deep: #b48f5e;
    --ink: #141210;
    --photo-dark: #1c1e24;
    --photo-mid: #3a3c44;
    --photo-light: #c9ab80;
  }
  * { margin: 0; padding: 0; box-sizing: border-box; }
  html, body {
    width: 1200px;
    height: 900px;
    overflow: hidden;
    background: var(--backdrop);
    font-family: "Open Sans", Arial, sans-serif;
    color: var(--ink);
  }
  .canvas {
    position: relative;
    width: 1200px;
    height: 900px;
  }
  .card {
    position: absolute;
    width: 556px;
    height: 342px;
    background: linear-gradient(135deg, var(--gold-light) 0%, var(--gold-mid) 50%, var(--gold-deep) 100%);
    box-shadow: 0 10px 28px rgba(0,0,0,0.18);
    overflow: hidden;
  }
  .card--front { left: 238px; top: 62px; }
  .card--back { left: 458px; top: 518px; width: 560px; height: 344px; }

  .profile-photo {
    position: absolute;
    left: 0;
    top: 0;
    width: 267px;
    height: 342px;
    background: linear-gradient(180deg, var(--photo-light) 0%, var(--photo-mid) 35%, var(--photo-dark) 100%);
  }

  .contact {
    position: absolute;
    left: 280px;
    top: 78px;
    width: 264px;
    text-align: center;
  }
  .contact__name {
    font-size: 27px;
    font-weight: 600;
    letter-spacing: 0.2px;
    margin-bottom: 28px;
  }
  .contact__line {
    font-size: 14px;
    line-height: 24px;
  }
  .contact__address {
    margin-top: 24px;
    font-size: 14px;
    line-height: 22px;
  }

  .brand {
    position: absolute;
    left: 0;
    right: 0;
    top: 124px;
    text-align: center;
    font-weight: 700;
    color: var(--ink);
  }
  .brand__mark {
    display: block;
    width: 30px;
    height: 30px;
    margin: 0 auto 14px;
    background: var(--ink);
  }
  .brand__name {
    font-size: 46px;
    letter-spacing: 7px;
    line-height: 1;
    text-transform: uppercase;
  }
  .brand__tagline {
    margin-top: 6px;
    font-size: 18px;
    letter-spacing: 5.8px;
    text-transform: uppercase;
  }
</style>
</head>
<body>
<main class="canvas">
  <section class="card card--front">
    <div class="profile-photo" role="img" aria-label="Profile photo of the card holder"></div>
    <div class="contact">
      <h1 class="contact__name">Daniel Hart</h1>
      <p class="contact__line">01483 556172</p>
      <p class="contact__line">info@norvanegroup.com</p>
      <p class="contact__address">Fenwick Lodge, Copse Lane,<br>Ashcombe Vale, GU14 3TP</p>
    </div>
  </section>

  <section class="card card--back">
    <div class="brand">
      <span class="brand__mark"></span>
      <p class="brand__name">Norvane</p>
      <p class="brand__tagline">Workplace Services</p>
    </div>
  </section>
</main>
</body>
</html>
```